Accounting firm needing business card / letterhead designed
Marcus L. Trenholm, CPA
marcus@veltrowledger.com
www.veltrowledger.com
842 E Alder Ave Halvern, NE 43827
738-562-0974

```html
<!DOCTYPE html>
<html lang="en">
<head>
<meta charset="utf-8">
<title>Veltro Ledger — Business Card</title>
<link href="https://fonts.googleapis.com/css2?family=Roboto:wght@400;500&family=Roboto+Condensed:wght@700&display=swap" rel="stylesheet">
<style>
  :root {
    --navy: #252060;
    --green: #7dbb33;
    --paper: #f7f7f5;
    --ink: #3d3d3d;
    --backdrop: #e4e4e4;
  }
  * { margin: 0; padding: 0; box-sizing: border-box; }
  html, body { width: 1200px; height: 960px; overflow: hidden; }
  body {
    background: var(--backdrop);
    font-family: "Roboto", Arial, sans-serif;
    position: relative;
  }
  .card {
    position: absolute;
    width: 600px;
    height: 343px;
    overflow: hidden;
  }
  .card--front { left: 314px; top: 113px; background: var(--paper); }
  .card--back { left: 311px; top: 472px; background: var(--navy); }

  .brand-name {
    position: absolute;
    font-family: "Roboto", Arial, sans-serif;
    font-weight: 500;
    letter-spacing: 3px;
    white-space: nowrap;
  }
  .card--front .brand-name {
    right: 34px; top: 58px;
    font-size: 38px;
    color: var(--navy);
  }
  .card--back .brand-name {
    left: 0; right: 0; top: 118px;
    text-align: center;
    font-size: 54px;
    color: #ffffff;
  }

  .name-band { position: absolute; left: 0; top: 192px; width: 600px; height: 58px; }
  .holder-name {
    position: absolute; left: 34px; top: 207px;
    font-family: "Roboto Condensed", "Arial Narrow", sans-serif;
    font-weight: 700; font-size: 21px;
    color: var(--green);
    white-space: nowrap;
  }
  .address {
    position: absolute; left: 34px; top: 275px;
    font-style: normal;
    font-size: 14px; line-height: 18px;
    color: var(--ink);
  }
  .contact-list {
    position: absolute; right: 34px; top: 255px;
    list-style: none;
    font-size: 14px; line-height: 19px;
    color: var(--ink);
    text-align: right;
  }
  .contact-list li { display: flex; align-items: center; justify-content: flex-end; gap: 6px; }
  .contact-list svg { width: 13px; height: 13px; fill: var(--navy); flex: none; }

  .back-url {
    position: absolute; left: 0; right: 0; top: 282px;
    text-align: center;
    font-size: 14px; letter-spacing: 6px;
    color: #ffffff;
  }
</style>
</head>
<body>
  <section class="card card--front" aria-label="Business card front">
    <div class="brand-name">VELTRO LEDGER</div>

    <svg class="name-band" viewBox="0 0 600 58" aria-hidden="true">
      <polygon points="0,0 600,0 600,14 306,14 261,57 0,57" fill="var(--navy)"/>
      <polygon points="314,15 600,15 600,22 307,22" fill="var(--green)"/>
    </svg>
    <div class="holder-name">Marcus L. Trenholm, CPA</div>

    <address class="address">
      842 E Alder Ave<br>
      Halvern, NE 43827
    </address>

    <ul class="contact-list">
      <li>738-562-0974
        <svg viewBox="0 0 24 24" aria-hidden="true"><path d="M6.6 10.8a15 15 0 0 0 6.6 6.6l2.2-2.2c.3-.3.7-.4 1-.2 1.1.4 2.3.6 3.6.6.6 0 1 .4 1 1V20c0 .6-.4 1-1 1A17 17 0 0 1 3 4c0-.6.4-1 1-1h3.5c.6 0 1 .4 1 1 0 1.3.2 2.5.6 3.6.1.3 0 .7-.2 1z"/></svg>
      </li>
      <li>marcus@veltrowledger.com
        <svg viewBox="0 0 24 24" aria-hidden="true"><path d="M2 5h20v14H2z M3 6l9 7 9-7" stroke="#fff" stroke-width="1.5"/></svg>
      </li>
      <li>www.veltrowledger.com
        <svg viewBox="0 0 24 24" aria-hidden="true"><circle cx="12" cy="12" r="10"/><path d="M2 12h20M12 2c3 3 3 17 0 20M12 2c-3 3-3 17 0 20" stroke="#fff" stroke-width="1.5" fill="none"/></svg>
      </li>
    </ul>
  </section>

  <section class="card card--back" aria-label="Business card back">
    <div class="brand-name">VELTRO LEDGER</div>
    <div class="back-url">www.veltrowledger.com</div>
  </section>
</body>
</html>
```